Business Cards for new orthopaedic surgery practice

My husband and I are starting our own orthopaedic surgery practice. We are looking for a business card that is uniform, but one will have my name/title and the other will have his. You can just create one design with my name on it for now. But when I choose your design as the winning design I will ask that you add another copy with his name/title.

We are looking for classy, simple, elite all in one. We like dark blues/a little gold/yellow. Something that goes with our logo. We want our logo incorporated. Here is all the info you need:
Business name: RV Bone & Vitality Center
Location: 38517 North Willowmere Ave
Palm Hollow, FL 33490
Phone: 954-218-4063
Fax: 954-582-7341
Email: info@myrvbonecare.example

Names: Lydia Vance, M.D.
Board Certified Hand and Upper Extremity Surgeon

Ebo Dansu, M.D.
Board Certified Hip & Knee Replacement/General Orthopaedic Surgeon

Can decide what you want to put on the back. Maybe a slogan:
Grounded in Care. Centered on You

I am just going to upload our logo. The only thing is if we select you as the winning design, the location, and phone numbers may change. We will need your help to update that once fully solidified.

Industry/Entity Type

Medical

Contact Information for Business Card

Colors
0054AA
0677BA
7BADD7
CADEEF
E8F1F8
0094D4
00A9DD
6FCCEA
C7EBF8
E9F6FB

Requirements
Must have
• class, appeal,
Should not have
• We want to air on the side of masculine if we are looking at masculine vs. feminine feel. But we still want it classy, sophisticated, and something we will love

```html
<!DOCTYPE html>
<html lang="en">
<head>
<meta charset="utf-8">
<title>RV Bone &amp; Vitality Center – Business Card</title>
<link rel="stylesheet" href="https://fonts.googleapis.com/css2?family=Arimo:wght@400&family=Cinzel:wght@700&display=swap">
<style>
  :root {
    --backdrop: #e4e4e4;
    --paper: #ffffff;
    --navy: #1e2d5a;
    --navy-top: #283d6b;
    --navy-bottom: #1c2850;
    --ink: #4a4a4a;
    --gold: #c5a05a;
    --white: #ffffff;
  }
  * { margin: 0; padding: 0; box-sizing: border-box; }
  html, body { width: 1200px; height: 1200px; overflow: hidden; }
  body { background: var(--backdrop); position: relative; font-family: "Arimo", Arial, sans-serif; }

  .card { position: absolute; width: 687px; height: 393px; overflow: hidden; }
  .card--front { left: 267px; top: 159px; background: var(--paper); }
  .card--back {
    left: 262px; top: 653px;
    background: linear-gradient(180deg, var(--navy-top), var(--navy-bottom));
  }

  .address { position: absolute; left: 35px; top: 94px; color: var(--ink); font-size: 16px; line-height: 21px; }
  .contacts { position: absolute; left: 35px; top: 141px; list-style: none; color: var(--ink); font-size: 16px; line-height: 21px; }
  .contacts li { display: flex; align-items: center; gap: 11px; }
  .contacts svg { width: 14px; height: 14px; fill: var(--navy); flex: none; }

  .doctor-name {
    position: absolute; left: 35px; top: 245px;
    font-family: "Cinzel", "Times New Roman", serif; font-weight: 700;
    font-size: 22px; letter-spacing: 0.5px; color: var(--navy);
  }
  .doctor-title { position: absolute; left: 35px; top: 274px; color: var(--gold); font-size: 16px; line-height: 20px; }

  .brand-front {
    position: absolute; left: 380px; top: 100px; width: 290px;
    display: flex; flex-direction: column; align-items: center; gap: 18px;
  }
  .brand-dot { width: 54px; height: 54px; border-radius: 50%; background: var(--navy); }
  .brand-name {
    font-family: "Cinzel", "Times New Roman", serif; font-weight: 700;
    text-align: center; line-height: 1.15;
  }
  .brand-front .brand-name { color: var(--navy); font-size: 34px; }

  .brand-back {
    position: absolute; left: 0; right: 0; top: 150px;
    display: flex; justify-content: center;
  }
  .brand-back .brand-name { color: var(--white); font-size: 30px; letter-spacing: 1px; }

  .slogan {
    position: absolute; left: 0; right: 0; top: 337px; text-align: center;
    color: var(--gold); font-size: 15.5px; letter-spacing: 3.2px; text-transform: uppercase;
  }
</style>
</head>
<body>
  <section class="card card--front">
    <p class="address">38517 North Willowmere Ave<br>Palm Hollow, FL 33490</p>
    <ul class="contacts">
      <li><svg viewBox="0 0 16 16" aria-hidden="true"><path d="M3.6 1.2l2.2 2.6-1.3 1.6c.9 2 2.3 3.4 4.2 4.3l1.6-1.3 2.6 2.2-1.2 2.2C7 12.6 3.3 8.9 1.4 2.5z"/></svg>954-218-4063</li>
      <li><svg viewBox="0 0 16 16" aria-hidden="true"><path d="M4 1h7v4H4zM1 6h14v7h-2v-3H3v3H1zM4 11h8v4H4z"/></svg>954-582-7341</li>
      <li><svg viewBox="0 0 16 16" aria-hidden="true"><path d="M1 4h14v9H1zM2 5l6 4.5L14 5v-.2H2z" fill-rule="evenodd"/></svg>info@myrvbonecare.example</li>
      <li><svg viewBox="0 0 16 16" aria-hidden="true"><path d="M8 1a7 7 0 100 14A7 7 0 008 1zm0 1.5a5.5 5.5 0 015.4 4.5H10l-1-2-2 1-1-2.3A5.5 5.5 0 018 2.5zM3 9.5h3l1.5 2-1 2A5.5 5.5 0 013 9.5z"/></svg>www.myrvbonecare.example</li>
    </ul>
    <h1 class="doctor-name">LYDIA VANCE, M.D.</h1>
    <p class="doctor-title">Board Certified Hand and<br>Upper Extremity Surgeon</p>
    <div class="brand-front">
      <span class="brand-dot" aria-hidden="true"></span>
      <p class="brand-name">RV Bone &amp;<br>Vitality Center</p>
    </div>
  </section>

  <section class="card card--back">
    <div class="brand-back">
      <p class="brand-name">RV Bone &amp;<br>Vitality Center</p>
    </div>
    <p class="slogan">Grounded in Care. Centered on You</p>
  </section>
</body>
</html>
```